Vindgerdi - Start-up company selling electricity

Hello let me tell you about Vindgerdi.

Vindgerdi is start-up company selling electricity in Iceland. The operations of the company consist of making power usage forecasts for our customers, purchasing the electricity wholesale from the energy producers, and selling the electricity to the consumer. We are focused on tech by using optimization and machine learning to minimize electricity prices to our customers. Our marketing strategy is to portray a tech company mindset and to show dedication to driving down the electricity price on the market.

We need your help to make our website pop. Possible concepts to work with are as follows:

- Iceland the land of ice and fire
- Green energy
- Innovation
- Tech and data science

Link to our website: https://prufa.vindgerdi-example.is/
We are open to ideas.
Thank you!

Target Market(s)

Electricity consumers both homes and companies.

Number of Pages Required

1 page

Font styles to use
Serif
Sans Serif

```html
<!DOCTYPE html>
<html lang="en">
<head>
<meta charset="utf-8">
<title>Vindgerdi – Same electricity, just cheaper</title>
<link href="https://fonts.googleapis.com/css2?family=Raleway:wght@500;600;700&family=Roboto:wght@400;500&family=Ubuntu:wght@700&display=swap" rel="stylesheet">
<style>
:root{
  --navy:#0d2a4f;
  --blue:#0b4f9c;
  --red:#dc1f33;
  --ink:#111;
  --muted:#555;
  --rule:#c9d3de;
  --card-border:#c7c7c7;
  --footer:#1f1f1f;
  --footer-rule:#3a3a3a;
  --white:#fff;
}
*{margin:0;padding:0;box-sizing:border-box}
html,body{width:798px;height:1200px;overflow:hidden;background:var(--white)}
body{position:relative;font-family:'Roboto',sans-serif;color:var(--ink)}
.abs{position:absolute}

.hero{left:0;top:0;width:798px;height:427px;overflow:hidden}
.hero-photo{position:absolute;inset:0;background:
  radial-gradient(ellipse 60% 30% at 55% 18%,rgba(60,220,110,.75),transparent 70%),
  radial-gradient(ellipse 40% 20% at 42% 82%,rgba(40,190,90,.6),transparent 70%),
  linear-gradient(180deg,#0b1d3a 0%,#123a52 30%,#1d2c33 52%,#1a3a3c 72%,#25333d 100%)}
.brand{left:75px;top:14px;display:flex;align-items:center;gap:8px;color:var(--white);font-family:'Raleway',sans-serif;font-weight:700;font-size:15px}
.brand-dot{width:22px;height:22px;border-radius:50%;background:var(--white)}
.nav{right:75px;top:24px;display:flex;gap:30px}
.nav a{color:var(--white);text-decoration:none;font-family:'Raleway',sans-serif;font-weight:500;font-size:9.5px;letter-spacing:.3px}
.hero-title{left:0;width:798px;top:196px;text-align:center;color:var(--white);font-family:'Ubuntu',sans-serif;font-weight:700;font-size:26px}
.slide-arrow{top:194px;width:40px;height:40px;border:1.2px solid var(--white);border-radius:50%}
.slide-arrow svg{position:absolute;left:13px;top:12px}
.dots{left:379px;top:384px;display:flex;gap:6px;align-items:center}
.dots span{width:4px;height:4px;border-radius:50%;background:var(--white)}
.dots span.on{width:8px;height:8px;background:none;border:1px solid var(--white)}

.vline{width:1px;background:var(--rule)}
.welcome{left:0;width:798px;top:527px;text-align:center;font-family:'Raleway',sans-serif;font-weight:700;font-size:17px;letter-spacing:.3px}
.btn{top:564px;width:116px;height:29px;border-radius:15px;color:var(--white);font-family:'Raleway',sans-serif;font-weight:500;font-size:10.5px;display:flex;align-items:center;justify-content:center;letter-spacing:.3px}
.btn-company{left:276px;background:var(--red)}
.btn-home{left:406px;background:var(--blue)}

.card{top:694px;width:257px;height:173px;border:1px solid var(--card-border);border-radius:10px;text-align:center}
.card h2{margin-top:24px;font-family:'Raleway',sans-serif;font-weight:700;font-size:16.5px;letter-spacing:.3px}
.price{position:absolute;top:56px;text-align:left}
.price b{display:block;color:var(--blue);font-family:'Raleway',sans-serif;font-weight:700;font-size:22px}
.price small{display:block;margin-top:6px;color:var(--muted);font-size:9.5px}
.price-note{position:absolute;left:131px;top:117px;font-family:'Raleway',sans-serif;font-weight:500;font-size:10px}
.compare{position:absolute;left:0;width:100%;top:144px;font-family:'Raleway',sans-serif;font-weight:500;font-size:12.5px}
.card p{margin:18px auto 0;width:210px;font-family:'Raleway',sans-serif;font-weight:500;font-size:10.2px;line-height:17px}

.footer{left:0;top:927px;width:798px;height:273px;background:var(--footer);color:var(--white)}
.company-info{position:absolute;top:16px;width:100%;text-align:center;font-weight:500;font-size:10px;line-height:20px}
.frule{position:absolute;left:74px;width:650px;height:1px;background:var(--footer-rule)}
.contact{position:absolute;top:126px;display:flex;align-items:center;gap:22px;font-weight:500;font-size:10px;line-height:20px}
.contact-icon{width:44px;height:44px;border:2px solid var(--blue);border-radius:50%;display:flex;align-items:center;justify-content:center;flex:none}
.csep{position:absolute;top:114px;width:1px;height:76px;background:var(--footer-rule)}
.copyright{position:absolute;top:236px;width:100%;text-align:center;font-size:10px}
</style>
</head>
<body>

<header class="hero abs">
  <div class="hero-photo" role="img" aria-label="Photograph of the northern lights over a mountain and a reflective black-sand beach at night"></div>
  <div class="brand abs"><span class="brand-dot"></span>Vindgerdi</div>
  <nav class="nav abs">
    <a href="#">Terms of business</a>
    <a href="#">Question &amp; Answer</a>
    <a href="#">About Vindgerdi</a>
  </nav>
  <h1 class="hero-title abs">Same electricity ~ just cheaper!</h1>
  <div class="slide-arrow abs" style="left:19px"><svg width="14" height="16" viewBox="0 0 14 16"><path d="M9 1 2 8l7 7" fill="none" stroke="#fff" stroke-width="1.5"/></svg></div>
  <div class="slide-arrow abs" style="left:739px"><svg width="14" height="16" viewBox="0 0 14 16"><path d="M4 1l7 7-7 7" fill="none" stroke="#fff" stroke-width="1.5"/></svg></div>
  <div class="dots abs"><span class="on"></span><span></span><span></span><span></span></div>
</header>

<svg class="abs" style="left:392px;top:414px" width="14" height="22" viewBox="0 0 14 22"><rect x="1" y="1" width="12" height="20" rx="6" fill="#fff" stroke="#0b4f9c" stroke-width="1.2"/><line x1="7" y1="5" x2="7" y2="9" stroke="#0b4f9c" stroke-width="1.4"/></svg>
<div class="vline abs" style="left:399px;top:436px;height:34px"></div>

<svg class="abs" style="left:388px;top:483px" width="24" height="30" viewBox="0 0 24 30"><rect x="5" y="0" width="3" height="8" rx="1" fill="#0d2a4f"/><rect x="16" y="0" width="3" height="8" rx="1" fill="#0d2a4f"/><path d="M1 8h22v3c0 6-4 10-9 10v3h-4v-3c-5 0-9-4-9-10z" fill="#0d2a4f"/><rect x="11" y="23" width="2" height="6" fill="#0d2a4f"/></svg>

<h2 class="welcome abs">WELCOME TO BUSINESS</h2>
<div class="btn btn-company abs">COMPANY</div>
<div class="btn btn-home abs">HOME</div>

<div class="vline abs" style="left:402px;top:604px;height:54px"></div>
<div class="abs" style="left:233px;top:670px;width:332px;height:1px;background:var(--rule)"></div>
<svg class="abs" style="left:388px;top:656px" width="28" height="28" viewBox="0 0 28 28"><circle cx="14" cy="14" r="13" fill="#fff" stroke="#dbe5f0"/><circle cx="14" cy="14" r="9.5" fill="#0b4f9c"/><path d="M10 12.5l4 4 4-4" fill="none" stroke="#fff" stroke-width="1.6"/></svg>

<svg class="abs" style="left:194px;top:655px" width="32" height="28" viewBox="0 0 32 28"><ellipse cx="17" cy="15" rx="12" ry="9" fill="#0d2a4f"/><circle cx="13" cy="4" r="3" fill="#0d2a4f"/><rect x="9" y="20" width="4" height="7" fill="#0d2a4f"/><rect x="20" y="20" width="4" height="7" fill="#0d2a4f"/><rect x="28" y="12" width="4" height="6" rx="1" fill="#0d2a4f"/><path d="M5 13c-3 0-4-2-3-3" fill="none" stroke="#0d2a4f" stroke-width="1.5"/></svg>
<svg class="abs" style="left:580px;top:655px" width="18" height="28" viewBox="0 0 18 28"><path d="M2 0h11l-3 10h7L5 28l3-13H1z" fill="#0d2a4f"/></svg>

<section class="card abs" style="left:82px">
  <h2>PRICE LIST</h2>
  <div class="price" style="left:25px"><b>6.95</b><small>ISK / kWh</small></div>
  <div class="price" style="left:134px"><b>6.22</b><small>ISK / kWh</small></div>
  <div class="price-note">electric acceleration</div>
  <div class="compare">Make a price comparison</div>
</section>

<section class="card abs" style="left:460px">
  <h2>THE FUTURE IS EXCITING</h2>
  <p>Let's make the electricity system smarter together. Vindgerdi uses artificial intelligence, data science and automation to minimize costs and promote eccentricity</p>
</section>

<footer class="footer abs">
  <div class="company-info">Vindgerdi ehf<br>ID number: 000000-0000<br>VAT number: 100000</div>
  <div class="frule" style="top:93px"></div>

  <div class="contact" style="left:98px">
    <div class="contact-icon"><svg width="16" height="20" viewBox="0 0 16 20"><path d="M8 0a8 8 0 0 1 8 8c0 5-8 12-8 12S0 13 0 8a8 8 0 0 1 8-8z" fill="#fff"/><circle cx="8" cy="8" r="3" fill="#1f1f1f"/></svg></div>
    <div>Address:<br>Lækjarvík 8 170<br>Norðurnes</div>
  </div>
  <div class="csep" style="left:292px"></div>
  <div class="contact" style="left:325px">
    <div class="contact-icon"><svg width="20" height="20" viewBox="0 0 20 20"><path d="M4 1l4 4-2 3c1 3 3 5 6 6l3-2 4 4-3 3C8 19 1 12 1 4z" fill="#fff"/></svg></div>
    <div>Telephone:<br>555-0190</div>
  </div>
  <div class="csep" style="left:475px"></div>
  <div class="contact" style="left:508px">
    <div class="contact-icon"><svg width="22" height="16" viewBox="0 0 22 16"><rect x="1" y="1" width="20" height="14" fill="none" stroke="#fff" stroke-width="1.6"/><path d="M1 1l10 8 10-8M1 15l7-7m13 7-7-7" fill="none" stroke="#fff" stroke-width="1.6"/></svg></div>
    <div>Email:<br>hallo@vindgerdi-example.is</div>
  </div>

  <div class="frule" style="top:211px"></div>
  <div class="copyright">Copyright © Vindgerdi 2021 All rights reserved</div>
</footer>

</body>
</html>
```